Verodex business card

Business card for sustainable investment company called "Verodex". Verodex is an exchange platform selling carbon credits between buyers and sellers. Carbon Credits are an environmental commodity for reducing global carbon emissions.

the card should obviously have our logo and the theme should be sustainability/environment mixed with a trading platform.

Contact Information for Business Card

Logo, Name, Title, Phone, Email

Colors
0054AA
0677BA
7BADD7
CADEEF
E8F1F8
0094D4
00A9DD
6FCCEA
C7EBF8
E9F6FB
00AB8E
00BBA5
67D7C9
C6EFE9
E9F9F6
59FF00
82FF00
B8FF75
E3FFCB
F4FFEA

```html
<!DOCTYPE html>
<html lang="en">
<head>
<meta charset="utf-8">
<title>Verodex business card</title>
<link href="https://fonts.googleapis.com/css2?family=Montserrat:wght@400;500;600;700&display=swap" rel="stylesheet">
<style>
  :root {
    --navy: #152a52;
    --ink: #1b2d4f;
    --sky: #00a9dd;
    --sky-light: #6fccea;
    --blue: #0677ba;
    --blue-deep: #4a6fc4;
    --paper: #ffffff;
    --backdrop: #e4e7ec;
    --text: #1e1e24;
  }
  * { margin: 0; padding: 0; box-sizing: border-box; }
  html, body { width: 1200px; height: 900px; overflow: hidden; }
  body {
    background: var(--backdrop);
    font-family: "Montserrat", Arial, sans-serif;
    position: relative;
  }
  .card {
    position: absolute;
    left: 260px;
    width: 680px;
    height: 388px;
    box-shadow: 0 10px 28px rgba(0,0,0,0.18);
    overflow: hidden;
  }
  .card-front { top: 50px; background: var(--navy); }
  .card-back { top: 462px; background: var(--paper); }

  .brand {
    position: absolute;
    display: flex;
    align-items: center;
    gap: 18px;
    left: 50%;
    transform: translateX(-50%);
    white-space: nowrap;
  }
  .brand-dot {
    width: 46px; height: 46px;
    border-radius: 50%;
    background: var(--sky);
  }
  .brand-name {
    font-weight: 600;
    font-size: 62px;
    letter-spacing: 2px;
    line-height: 1;
  }
  .card-front .brand { top: 163px; }
  .card-front .brand-name { color: var(--paper); }
  .card-back .brand { top: 92px; }
  .card-back .brand-name { color: var(--ink); font-size: 58px; }

  .person {
    position: absolute;
    top: 196px;
    right: 360px;
    text-align: right;
  }
  .person-name {
    font-weight: 700;
    font-size: 24px;
    letter-spacing: 0.5px;
    color: var(--ink);
  }
  .person-name .first { color: var(--sky); }
  .person-title {
    font-size: 17px;
    color: var(--text);
    margin-top: 2px;
  }
  .divider {
    position: absolute;
    left: 334px;
    top: 180px;
    width: 1.5px;
    height: 86px;
    background: var(--sky);
  }
  .contacts {
    position: absolute;
    left: 350px;
    top: 180px;
    list-style: none;
  }
  .contacts li {
    display: flex;
    align-items: center;
    gap: 10px;
    font-size: 17px;
    color: var(--text);
    height: 29px;
  }
  .contacts svg { width: 18px; height: 18px; flex: none; }
  .card-bands { position: absolute; left: 0; top: 0; }
</style>
</head>
<body>
  <section class="card card-front">
    <div class="brand">
      <span class="brand-dot"></span>
      <span class="brand-name">VERODEX</span>
    </div>
  </section>

  <section class="card card-back">
    <div class="brand">
      <span class="brand-dot"></span>
      <span class="brand-name">VERODEX</span>
    </div>

    <div class="person">
      <div class="person-name"><span class="first">DANIEL</span> HARTWIG</div>
      <div class="person-title">Co-Founder</div>
    </div>

    <span class="divider"></span>

    <ul class="contacts">
      <li>
        <svg viewBox="0 0 24 24" aria-hidden="true"><path fill="#0094d4" d="M6.6 10.8a15.1 15.1 0 0 0 6.6 6.6l2.2-2.2c.3-.3.7-.4 1-.2 1.1.4 2.3.6 3.6.6.6 0 1 .4 1 1V20c0 .6-.4 1-1 1A17 17 0 0 1 3 4c0-.6.4-1 1-1h3.5c.6 0 1 .4 1 1 0 1.3.2 2.5.6 3.6.1.3 0 .7-.2 1z"/></svg>
        555-204-7381
      </li>
      <li>
        <svg viewBox="0 0 24 24" aria-hidden="true"><rect x="2" y="5" width="20" height="14" rx="1" fill="#0094d4"/><path d="M3 6l9 7 9-7" fill="none" stroke="#fff" stroke-width="1.6"/></svg>
        info@verodex.com
      </li>
      <li>
        <svg viewBox="0 0 24 24" aria-hidden="true"><circle cx="12" cy="12" r="10" fill="#0094d4"/><path d="M2 12h20M12 2c3 3 3 17 0 20M12 2c-3 3-3 17 0 20" fill="none" stroke="#fff" stroke-width="1.2"/></svg>
        www.verodex.com
      </li>
    </ul>

    <svg class="card-bands" width="680" height="388" viewBox="0 0 680 388" aria-hidden="true">
      <defs>
        <linearGradient id="band-gradient" x1="0" y1="0" x2="1" y2="0">
          <stop offset="0" stop-color="#6fccea"/>
          <stop offset="0.55" stop-color="#00a9dd"/>
          <stop offset="1" stop-color="#4a6fc4"/>
        </linearGradient>
      </defs>
      <polygon points="0,374 470,326 470,388 0,388" fill="url(#band-gradient)"/>
      <polygon points="480,300 680,236 680,388 466,388" fill="#152a52"/>
    </svg>
  </section>
</body>
</html>
```